Layout for site fence advertising - length approx. 250 cm x 125 cm

The advertising will later be printed on a PVC film and used for events or on sports fields.

Main services :
Your regional contact at
Real estate and business financing
independent insurance advice

```html
<!DOCTYPE html>
<html lang="en">
<head>
<meta charset="utf-8">
<title>Site Fence Banner – Brenner Vermögensberatung</title>
<link rel="stylesheet" href="https://fonts.googleapis.com/css2?family=Bebas+Neue&family=Montserrat:wght@400;500;600;700;800&display=swap">
<style>
  :root {
    --brand-blue: #1d4fc4;
    --brand-blue-deep: #163f9e;
    --ink: #1b1b1b;
    --paper: #f4f4f4;
    --stripe-grey: #6b6b6b;
    --white: #ffffff;
  }
  * { box-sizing: border-box; margin: 0; padding: 0; }
  html, body {
    width: 865px; height: 1200px; overflow: hidden;
    background: var(--white);
    font-family: "Montserrat", Arial, sans-serif;
  }
  .fence-banner {
    position: absolute; left: 30px; top: 399px;
    width: 805px; height: 403px; overflow: hidden;
    background: var(--paper);
    box-shadow: 0 18px 40px rgba(0,0,0,.35);
  }
  .banner-shapes { position: absolute; inset: 0; width: 805px; height: 403px; }

  .landscape-backdrop {
    position: absolute; left: 0; top: 0; width: 490px; height: 403px;
    background: linear-gradient(180deg, #efefef 0%, #dcdcdc 45%, #e6e6e6 100%);
    clip-path: polygon(0 0, 488px 0, 429px 403px, 0 403px);
  }
  .city-backdrop {
    position: absolute; left: 440px; top: 0; width: 365px; height: 403px;
    background: linear-gradient(180deg, #1f52c8 0%, #1a47ad 55%, #173f9a 100%);
    clip-path: polygon(63px 0, 365px 0, 365px 403px, 4px 403px);
  }
  .portrait {
    position: absolute; left: 521px; top: 115px; width: 250px; height: 288px;
    background: linear-gradient(180deg, #7a6a5e 0%, #5c4f48 35%, #2a2c38 70%, #1e202a 100%);
    border-radius: 110px 110px 0 0;
  }

  .headline { position: absolute; left: 42px; font-family: "Bebas Neue", Impact, sans-serif; line-height: 1; white-space: nowrap; }
  .headline--primary { top: 24px; font-size: 77px; color: var(--brand-blue); letter-spacing: -0.5px; }
  .headline--secondary { top: 89px; font-size: 64px; color: var(--ink); letter-spacing: -0.3px; }
  .headline--tertiary { top: 147px; font-size: 40.5px; color: var(--brand-blue); letter-spacing: -0.2px; }

  .service-list {
    position: absolute; top: 204px; font-size: 17px; font-weight: 500;
    color: var(--ink); letter-spacing: .3px; list-style: none; line-height: 25px;
  }
  .service-list--left { left: 42px; }
  .service-list--right { left: 263px; }
  .service-list li { display: flex; align-items: center; gap: 6px; }
  .service-list svg { width: 13px; height: 13px; flex: none; }

  .contact-band { position: absolute; left: 42px; top: 266px; color: var(--white); }
  .contact-band__label { font-size: 22.5px; font-weight: 400; letter-spacing: .6px; line-height: 1.1; white-space: nowrap; }
  .contact-band__phone { display: flex; align-items: center; gap: 12px; margin-top: 1px; font-size: 34px; font-weight: 700; letter-spacing: 1px; line-height: 1.1; white-space: nowrap; }
  .contact-band__phone svg { width: 24px; height: 24px; }

  .website { position: absolute; left: 42px; top: 343px; display: flex; align-items: center; gap: 16px; font-size: 29px; font-weight: 700; color: var(--ink); white-space: nowrap; }
  .website svg { width: 22px; height: 22px; }

  .company-mark { position: absolute; left: 508px; top: 30px; display: flex; align-items: center; color: var(--white); }
  .company-mark__dot { width: 66px; height: 66px; border: 3px solid var(--white); border-radius: 50%; }
  .company-mark__divider { width: 2px; height: 72px; background: var(--white); margin: 0 8px 0 13px; }
  .company-mark__name { font-size: 13.5px; font-weight: 600; line-height: 1.25; }
  .company-mark__tagline { font-size: 10px; font-weight: 500; }

  .person-name { position: absolute; left: 470px; top: 338px; width: 335px; height: 34px; display: flex; align-items: center; justify-content: center; font-size: 25px; font-weight: 600; color: var(--ink); letter-spacing: .3px; padding-left: 6px; white-space: nowrap; }
</style>
</head>
<body>
  <section class="fence-banner">
    <div class="landscape-backdrop" role="img" aria-label="Faded photo of a hillside town with vineyards and a castle ruin"></div>
    <div class="city-backdrop" role="img" aria-label="Blue-tinted photo of a riverside city with bridges"></div>

    <svg class="banner-shapes" viewBox="0 0 805 403" aria-hidden="true">
      <polygon points="490,0 497,0 438,403 431,403" fill="var(--stripe-grey)"/>
      <polygon points="0,263 453,263 442,336 0,336" fill="var(--brand-blue)"/>
      <line x1="42" y1="196" x2="440" y2="196" stroke="var(--ink)" stroke-width="2.5"/>
      <circle cx="441" cy="196" r="3.5" fill="var(--brand-blue)"/>
      <line x1="221" y1="209" x2="221" y2="256" stroke="var(--brand-blue)" stroke-width="1.5"/>
    </svg>

    <div class="portrait" role="img" aria-label="Portrait photo of the adviser in a dark suit and white shirt"></div>

    <svg class="banner-shapes" viewBox="0 0 805 403" aria-hidden="true">
      <polygon points="470,338 805,338 805,372 465,372" fill="var(--white)"/>
    </svg>

    <h1 class="headline headline--primary">REAL ESTATE AND</h1>
    <h2 class="headline headline--secondary">BUSINESS FINANCING</h2>
    <h3 class="headline headline--tertiary">INDEPENDENT INSURANCE ADVISER</h3>

    <ul class="service-list service-list--left">
      <li><svg viewBox="0 0 14 14"><rect x="1" y="2" width="11" height="11" fill="none" stroke="var(--brand-blue)" stroke-width="1.6"/><path d="M3.5 7.5l2.5 2.5 7-8" fill="none" stroke="var(--brand-blue)" stroke-width="1.8"/></svg>INVESTING</li>
      <li><svg viewBox="0 0 14 14"><rect x="1" y="2" width="11" height="11" fill="none" stroke="var(--brand-blue)" stroke-width="1.6"/><path d="M3.5 7.5l2.5 2.5 7-8" fill="none" stroke="var(--brand-blue)" stroke-width="1.8"/></svg>INSURANCE</li>
    </ul>
    <ul class="service-list service-list--right">
      <li><svg viewBox="0 0 14 14"><rect x="1" y="2" width="11" height="11" fill="none" stroke="var(--brand-blue)" stroke-width="1.6"/><path d="M3.5 7.5l2.5 2.5 7-8" fill="none" stroke="var(--brand-blue)" stroke-width="1.8"/></svg>FINANCING</li>
      <li><svg viewBox="0 0 14 14"><rect x="1" y="2" width="11" height="11" fill="none" stroke="var(--brand-blue)" stroke-width="1.6"/><path d="M3.5 7.5l2.5 2.5 7-8" fill="none" stroke="var(--brand-blue)" stroke-width="1.8"/></svg>LEASING</li>
    </ul>

    <div class="contact-band">
      <p class="contact-band__label">YOUR REGIONAL CONTACT AT</p>
      <p class="contact-band__phone">
        <svg viewBox="0 0 24 24"><path d="M6.6 10.8a15 15 0 0 0 6.6 6.6l2.2-2.2a1 1 0 0 1 1-.25 11.4 11.4 0 0 0 3.6.6 1 1 0 0 1 1 1V20a1 1 0 0 1-1 1A17 17 0 0 1 3 4a1 1 0 0 1 1-1h3.5a1 1 0 0 1 1 1c0 1.25.2 2.45.6 3.6a1 1 0 0 1-.25 1z" fill="var(--white)"/></svg>
        43 660 214 5089
      </p>
    </div>

    <p class="website">
      <svg viewBox="0 0 24 24"><circle cx="12" cy="12" r="10" fill="none" stroke="var(--brand-blue)" stroke-width="2.2"/><ellipse cx="12" cy="12" rx="4.5" ry="10" fill="none" stroke="var(--brand-blue)" stroke-width="2"/><line x1="2" y1="12" x2="22" y2="12" stroke="var(--brand-blue)" stroke-width="2"/></svg>
      www.der-brenner.at
    </p>

    <div class="company-mark">
      <span class="company-mark__dot"></span>
      <span class="company-mark__divider"></span>
      <div>
        <p class="company-mark__name">Brenner Vermögensberatung GmbH</p>
        <p class="company-mark__tagline">Finanzieren, Versichern, Vorsorgen</p>
      </div>
    </div>

    <p class="person-name">MARKUS BRENNER</p>
  </section>
</body>
</html>
```